Meridale Bed Company Needs Business Card

Looking for a very nice looking business card. Creative but not extravagant. We sell beds and pillows across the U.S. and need something professional but catchy. I have attached the logo.

Name : Devin Holt
Title : President
Phone : (800) 471-2960
Email: sleep@quilmora.com
Website: www.quilmora.com

Can be single-sided or double-sided
horizontal or vertical

Can use Blues/Greys

Target Market(s)

Mass Market

Industry/Entity Type

Retail

Contact Information for Business Card

Name : Devin Holt
Title : President
Phone : (800) 471-2960
Email: sleep@quilmora.com
Website: www.quilmora.com

Requirements
Must have
• Clean, Modern, Smooth
• Can use Blues/Greys
• On the other side without the information - have something simple like www.quilmora.com or our logo
Nice to have
• Surprise me
Should not have
• Nothing crazy, nothing cluttered

```html
<!DOCTYPE html>
<html lang="en">
<head>
<meta charset="utf-8">
<title>Quilmora Business Card</title>
<link rel="stylesheet" href="https://fonts.googleapis.com/css2?family=Open+Sans:wght@300;400;700&display=swap">
<style>
  :root {
    --brand-blue: #35a3d4;
    --brand-blue-light: #c4e4f3;
    --card-white: #ffffff;
    --backdrop: #eeeeec;
  }
  html, body {
    margin: 0;
    padding: 0;
    width: 1200px;
    height: 1200px;
    overflow: hidden;
    background: var(--backdrop);
  }
  .canvas {
    position: relative;
    width: 1200px;
    height: 1200px;
  }
  .card {
    position: absolute;
    left: 212px;
    width: 775px;
    height: 430px;
    display: block;
  }
  .card--front { top: 114px; }
  .card--back  { top: 656px; }
  .fill-blue  { fill: var(--brand-blue); }
  .fill-white { fill: var(--card-white); }
  .company-name {
    font-family: "Open Sans", sans-serif;
    font-weight: 400;
    font-size: 50px;
    fill: var(--brand-blue);
  }
  .holder-name {
    font-family: "Open Sans", sans-serif;
    font-size: 26px;
    fill: var(--card-white);
  }
  .holder-name__first { font-weight: 300; }
  .holder-name__last  { font-weight: 700; }
  .holder-title {
    font-family: "Open Sans", sans-serif;
    font-weight: 400;
    font-size: 15.5px;
    letter-spacing: 0.5px;
    fill: var(--card-white);
  }
  .contact-text {
    font-family: "Open Sans", sans-serif;
    font-weight: 400;
    font-size: 12.5px;
    fill: var(--card-white);
  }
  .icon-line {
    fill: none;
    stroke: var(--card-white);
    stroke-width: 1.6;
  }
</style>
</head>
<body>
<main class="canvas">

  <!-- Front side: company name with decorative area -->
  <svg class="card card--front" viewBox="0 0 646 358" xmlns="http://www.w3.org/2000/svg" aria-label="Quilmora business card, front">
    <defs>
      <linearGradient id="front-accent-tone" x1="0" y1="0" x2="1" y2="0">
        <stop offset="0" stop-color="#ffffff"/>
        <stop offset="1" stop-color="#35a3d4"/>
      </linearGradient>
    </defs>
    <rect class="fill-white" width="646" height="358"/>
    <rect class="accent-area" x="295" y="0" width="351" height="358" fill="url(#front-accent-tone)" role="img" aria-label="Decorative blue sweeping curves along the right edge"/>
    <text class="company-name" x="31" y="300">quilmora</text>
  </svg>

  <!-- Back side: contact details -->
  <svg class="card card--back" viewBox="0 0 646 358" xmlns="http://www.w3.org/2000/svg" aria-label="Quilmora business card, back">
    <defs>
      <linearGradient id="back-accent-tone" x1="0" y1="0" x2="1" y2="0">
        <stop offset="0" stop-color="#35a3d4"/>
        <stop offset="1" stop-color="#c4e4f3"/>
      </linearGradient>
    </defs>
    <rect class="fill-blue" width="646" height="358"/>
    <rect class="accent-area" x="295" y="0" width="351" height="358" fill="url(#back-accent-tone)" role="img" aria-label="Decorative white sweeping curves along the right edge"/>

    <text class="holder-name" x="21" y="60"><tspan class="holder-name__first">Devin </tspan><tspan class="holder-name__last">Holt</tspan></text>
    <text class="holder-title" x="54" y="87">PRESIDENT</text>

    <g class="contact-row contact-row--phone">
      <rect class="icon-line" x="37" y="156" width="13" height="26" rx="2"/>
      <line class="icon-line" x1="37" y1="161" x2="50" y2="161"/>
      <line class="icon-line" x1="37" y1="176" x2="50" y2="176"/>
      <text class="contact-text" x="79" y="175">(800) 471-2960</text>
    </g>

    <g class="contact-row contact-row--email">
      <rect class="icon-line" x="31" y="224" width="25" height="17"/>
      <polyline class="icon-line" points="31,224 43.5,235 56,224"/>
      <text class="contact-text" x="79" y="236">Sleep@quilmora.com</text>
    </g>

    <g class="contact-row contact-row--web">
      <circle class="icon-line" cx="43.5" cy="293" r="12.5"/>
      <ellipse class="icon-line" cx="43.5" cy="293" rx="5.5" ry="12.5"/>
      <line class="icon-line" x1="31" y1="293" x2="56" y2="293"/>
      <text class="contact-text" x="79" y="298">www.quilmora.com</text>
    </g>
  </svg>

</main>
</body>
</html>
```